Automotive component supplier needs a business card design

We need a business card design for our company called Velran Global Components Ltd based in the UK. We are a supplier of interior and exterior components to premium car manufacturers such as Corvel Ashby, Hadley Fenn, Marquist and Tavarelli. We would like to see a modern business card design that uses the colour blue.

Target Market(s)

Premium automotive car manufacturers.

Industry/Entity Type

Automotive

Contact Information for Business Card

Company Name : Velran Global Components Limited
Address: 17 Marlow Yard, Upper Heath, Warwick, CV31 8QL, United Kingdom
Web Address : www.velrancomponents-example.co.uk

Font styles to use
Other font styles liked:
• Helvetica

Colors
3176b5
0255a3
85acd3
cfdeed
cee9f5
85cae6
34a6d7
0692cd
9bcb3c

Requirements
Must have
• Clear company logo and a mixture of blue colours.
Nice to have
• A high quality modern image.
Should not have
• Multiple colours.

```html
<!DOCTYPE html>
<html lang="en">
<head>
<meta charset="utf-8">
<title>Velran Global Components – Business Card</title>
<link rel="stylesheet" href="https://fonts.googleapis.com/css2?family=Arimo:wght@400;700&display=swap">
<style>
  :root {
    --stage: #3b3531;
    --brand-blue: #0692cd;
    --text-blue: #0a8fcf;
    --accent-green: #9bcb3c;
    --card-white: #ffffff;
    --ink-white: #ffffff;
  }
  * { box-sizing: border-box; margin: 0; padding: 0; }
  html, body {
    width: 1200px; height: 780px; overflow: hidden;
    background: var(--stage);
    font-family: "Arimo", Helvetica, Arial, sans-serif;
  }
  .canvas {
    position: relative; width: 1200px; height: 780px;
    display: flex; align-items: center; justify-content: center; gap: 40px;
  }
  .card {
    position: relative; width: 540px; height: 309px; overflow: hidden;
    box-shadow: 0 14px 30px rgba(0,0,0,.45);
  }
  .card--front {
    background: var(--brand-blue);
    display: flex; align-items: center; justify-content: center;
  }
  .card--back { background: var(--card-white); }

  .wordmark {
    display: flex; flex-direction: column; align-items: flex-start;
    font-weight: 700; line-height: 1;
  }
  .wordmark__name { font-size: 66px; letter-spacing: 1px; }
  .wordmark__sub { font-size: 11.5px; letter-spacing: 2.6px; margin-top: 6px; margin-left: 3px; }
  .card--front .wordmark { color: var(--ink-white); }

  .card--back .wordmark {
    position: absolute; left: 30px; top: 110px; color: var(--brand-blue);
  }
  .card--back .wordmark__name { font-size: 48px; }
  .card--back .wordmark__sub { font-size: 8.5px; letter-spacing: 1.9px; margin-top: 5px; }

  .divider {
    position: absolute; left: 268px; top: 62px; width: 1px; height: 186px;
    background: var(--accent-green);
  }
  .contact {
    position: absolute; left: 284px; top: 66px; color: var(--text-blue);
    font-size: 12px; line-height: 1.3; white-space: nowrap;
  }
  .contact__name { font-size: 17px; font-weight: 700; letter-spacing: .4px; }
  .contact__role { color: var(--accent-green); font-size: 12.5px; margin-bottom: 8px; }
  .contact__address { margin-bottom: 8px; }
  .contact__list { list-style: none; }
  .contact__list li { display: flex; align-items: center; gap: 6px; height: 17px; white-space: nowrap; }
  .contact__icon { width: 13px; height: 13px; flex: none; }
</style>
</head>
<body>
<main class="canvas">
  <section class="card card--front" aria-label="Card front">
    <div class="wordmark">
      <span class="wordmark__name">VELRAN</span>
      <span class="wordmark__sub">GLOBAL COMPONENTS</span>
    </div>
  </section>

  <section class="card card--back" aria-label="Card back">
    <div class="wordmark">
      <span class="wordmark__name">VELRAN</span>
      <span class="wordmark__sub">GLOBAL COMPONENTS</span>
    </div>
    <div class="divider"></div>
    <div class="contact">
      <p class="contact__name">EMPLOYEE NAME</p>
      <p class="contact__role">Managing Director</p>
      <p class="contact__address">17 Marlow Yard, Upper Heath<br>Warwick, CV31 8QL<br>United Kingdom</p>
      <ul class="contact__list">
        <li>
          <svg class="contact__icon" viewBox="0 0 14 14" aria-hidden="true"><rect width="14" height="14" rx="2" fill="#9bcb3c"/><rect x="4.5" y="2.5" width="5" height="9" rx="1" fill="none" stroke="#fff" stroke-width="1.2"/><circle cx="7" cy="9.8" r=".7" fill="#fff"/></svg>
          (01) 5550 0142
        </li>
        <li>
          <svg class="contact__icon" viewBox="0 0 14 14" aria-hidden="true"><rect width="14" height="14" rx="2" fill="#9bcb3c"/><rect x="3" y="5.5" width="8" height="5" fill="none" stroke="#fff" stroke-width="1.2"/><rect x="4.5" y="2.5" width="5" height="3" fill="none" stroke="#fff" stroke-width="1"/></svg>
          (01) 5550 0143
        </li>
        <li>
          <svg class="contact__icon" viewBox="0 0 14 14" aria-hidden="true"><rect width="14" height="14" rx="2" fill="#9bcb3c"/><rect x="2.5" y="4" width="9" height="6.5" fill="none" stroke="#fff" stroke-width="1.1"/><path d="M2.5 4 7 8 11.5 4" fill="none" stroke="#fff" stroke-width="1.1"/></svg>
          info@velran-example.co.uk
        </li>
        <li>
          <svg class="contact__icon" viewBox="0 0 14 14" aria-hidden="true"><rect width="14" height="14" rx="7" fill="#9bcb3c"/><circle cx="7" cy="7" r="4.2" fill="none" stroke="#fff" stroke-width="1"/><ellipse cx="7" cy="7" rx="1.8" ry="4.2" fill="none" stroke="#fff" stroke-width=".9"/><path d="M2.8 7h8.4" stroke="#fff" stroke-width=".9"/></svg>
          www.velrancomponents-example.co.uk
        </li>
      </ul>
    </div>
  </section>
</main>
</body>
</html>
```